Business Card Design

New business card design

Target Market(s)

Residential & Commercial Property Managers

Industry/Entity Type

Plumbing Services

Contact Information for Business Card

Name - Rowan Keddle, title - Director, Phone Number - 0431 286 517, email - rowan@tbk-plumbing.com.au, Company ABN - 73 215 904 386,

Font styles to use
Sans Serif

Colors
0054AA
0677BA
7BADD7
CADEEF
E8F1F8

```html
<!DOCTYPE html>
<html lang="en">
<head>
<meta charset="utf-8">
<title>TBK Plumbing Services – Business Card</title>
<link href="https://fonts.googleapis.com/css2?family=Poppins:wght@300;400;600&display=swap" rel="stylesheet">
<style>
  :root {
    --backdrop: #232323;
    --sky: #24a8e0;
    --sky-deep: #1e96cf;
    --night: #1c232b;
    --white: #ffffff;
    --accent: #22a2dc;
    --taupe: #8a7d72;
    --soft: #cadeef;
  }
  * { margin: 0; padding: 0; box-sizing: border-box; }
  html, body {
    width: 1200px; height: 711px; overflow: hidden;
    background: var(--backdrop);
    font-family: "Poppins", sans-serif;
  }
  .canvas {
    position: relative; width: 1200px; height: 711px;
    display: flex; align-items: center; justify-content: center; gap: 40px;
  }
  .card {
    position: relative; width: 540px; height: 330px;
    border-radius: 4px;
    box-shadow: 0 14px 30px rgba(0,0,0,.55);
    overflow: hidden;
  }
  .card--front { background: var(--sky); }
  .card--back {
    background: var(--night);
    display: flex; flex-direction: column; align-items: center;
    padding-top: 40px; text-align: center;
  }
  .wordmark { color: var(--white); font-weight: 300; line-height: 1; }
  .card--front .brand { position: absolute; right: 44px; bottom: 70px; text-align: right; }
  .card--front .wordmark { font-size: 62px; letter-spacing: 2px; }
  .card--back .wordmark { font-size: 70px; letter-spacing: 2px; }
  .tagline {
    color: var(--white); font-weight: 300; font-size: 9px;
    letter-spacing: 6px; margin-top: 6px; opacity: .85;
  }
  .card--back .tagline { color: var(--taupe); opacity: 1; }
  .person { margin-top: 26px; font-size: 26px; line-height: 1; }
  .person__first { color: var(--accent); font-weight: 600; }
  .person__last { color: var(--taupe); font-weight: 300; }
  .role { color: var(--white); font-size: 12px; margin-top: 4px; }
  .abn { color: var(--accent); font-size: 12px; margin-top: 12px; letter-spacing: .5px; }
  .icons { display: flex; gap: 8px; margin-top: 10px; }
  .icon {
    width: 18px; height: 18px; border-radius: 4px; background: var(--accent);
    display: flex; align-items: center; justify-content: center;
  }
  .contact { color: var(--white); font-size: 11px; line-height: 1.55; margin-top: 8px; font-weight: 300; }
</style>
</head>
<body>
<main class="canvas">
  <section class="card card--front">
    <div class="brand">
      <div class="wordmark">tbk</div>
      <div class="tagline">plumbing services</div>
    </div>
  </section>

  <section class="card card--back">
    <div class="wordmark">tbk</div>
    <div class="tagline">plumbing services</div>
    <div class="person"><span class="person__first">Rowan</span> <span class="person__last">Keddle</span></div>
    <div class="role">Director</div>
    <div class="abn">ABN - 73 215 904 386</div>
    <div class="icons">
      <span class="icon" aria-label="Phone">
        <svg width="11" height="11" viewBox="0 0 24 24"><path fill="#fff" d="M6.6 10.8a15 15 0 0 0 6.6 6.6l2.2-2.2c.3-.3.7-.4 1-.2 1.1.4 2.3.6 3.6.6.6 0 1 .4 1 1V20c0 .6-.4 1-1 1A17 17 0 0 1 3 4c0-.6.4-1 1-1h3.5c.6 0 1 .4 1 1 0 1.3.2 2.5.6 3.6.1.3 0 .7-.2 1l-2.3 2.2z"/></svg>
      </span>
      <span class="icon" aria-label="Email">
        <svg width="11" height="11" viewBox="0 0 24 24"><rect x="2" y="5" width="20" height="14" rx="2" fill="none" stroke="#fff" stroke-width="2"/><path d="M3 6l9 7 9-7" fill="none" stroke="#fff" stroke-width="2"/></svg>
      </span>
      <span class="icon" aria-label="Website">
        <svg width="11" height="11" viewBox="0 0 24 24"><circle cx="12" cy="12" r="9" fill="none" stroke="#fff" stroke-width="2"/><path d="M3 12h18M12 3c3 3 3 15 0 18M12 3c-3 3-3 15 0 18" fill="none" stroke="#fff" stroke-width="1.6"/></svg>
      </span>
    </div>
    <div class="contact">
      0431 286 517<br>
      www.tbk-plumbing.com.au<br>
      rowan@tbk-plumbing.com.au
    </div>
  </section>
</main>
</body>
</html>
```